Business Card for beauty technology startup

Design Glimora Business Card for a Beauty, based on the website identity and colors (https://www.glimora-example.com).
Glimora is a beauty tech startup that gathers helpful product info for beauty lovers and consumers (such as availability on stores, price range and product reviews) for makeup products. The card design must be young, colorful but clean, and very modern.

Target Market(s)

woman, 15-35

Industry/Entity Type

Cosmetics

Contact Information for Business Card

Full Name, address, phone

Font styles to use
Other font styles liked:
• Advent Pro

Colors
e34297
86cfc6
ffffff
5c5c5c
e8e8e8
e667a6
b2b2b2

Requirements
Must have
• One full colored side with a creative design and another with card info
• Use Color palette: #95C5C5 and/or #D38AA5
• Use fonts: Advent Pro
• Use website identity: https://www.glimora-example.com
Nice to have
• If needed extra font: Roboto

```html
<!DOCTYPE html>
<html lang="en">
<head>
<meta charset="utf-8">
<title>Glimora Business Card</title>
<link rel="stylesheet" href="https://fonts.googleapis.com/css2?family=Advent+Pro:wght@300;400&family=Roboto:wght@400&family=Roboto+Condensed:wght@700&display=swap">
<style>
  :root {
    --rose: #b97f98;
    --rose-soft: #c894aa;
    --ink: #5c5c5c;
    --ink-dark: #3a3a3a;
    --paper: #f7f7f7;
    --backdrop: #e8e8e8;
    --white: #ffffff;
  }
  * { margin: 0; padding: 0; box-sizing: border-box; }
  html, body { width: 1200px; height: 886px; overflow: hidden; background: var(--backdrop); }
  .stage { position: relative; width: 1200px; height: 886px; }

  .card {
    position: absolute; top: 146px; width: 340px; height: 594px;
    border-radius: 22px; overflow: hidden;
    box-shadow: 0 10px 28px rgba(0,0,0,0.14);
  }

  /* Front side */
  .card-front { left: 190px; background: var(--rose); }
  .front-ring {
    position: absolute; left: 34px; top: 70px; width: 272px; height: 272px;
    border: 9px solid var(--rose-soft); border-radius: 50%;
  }
  .front-brand {
    position: absolute; left: 40px; bottom: 92px;
    font-family: "Advent Pro", sans-serif; font-weight: 300;
    font-size: 52px; letter-spacing: 12px; color: var(--white); line-height: 1;
  }
  .front-url {
    position: absolute; left: 42px; bottom: 62px;
    font-family: "Roboto", sans-serif; font-size: 13px;
    letter-spacing: 4.2px; color: var(--white);
  }

  /* Back side */
  .card-back { left: 670px; background: var(--paper); text-align: center; }
  .brand-dot {
    width: 74px; height: 74px; margin: 58px auto 0;
    border: 4px solid var(--rose); border-radius: 50%;
  }
  .back-brand {
    margin-top: 16px;
    font-family: "Advent Pro", sans-serif; font-weight: 300;
    font-size: 44px; letter-spacing: 10px; padding-left: 10px; color: var(--rose); line-height: 1;
  }
  .person-name {
    margin-top: 42px;
    font-family: "Roboto Condensed", sans-serif; font-weight: 700;
    font-size: 22px; color: var(--rose); letter-spacing: 0.5px;
  }
  .person-role {
    margin-top: 2px;
    font-family: "Roboto", sans-serif; font-size: 15px; color: var(--ink-dark);
  }
  .address {
    margin-top: 22px;
    font-family: "Roboto", sans-serif; font-size: 14px; line-height: 1.45; color: var(--ink);
  }
  .contact-rule { display: block; margin: 20px auto 0; }
  .contacts {
    margin-top: 16px;
    font-family: "Roboto", sans-serif; font-size: 14px; line-height: 1.45; color: var(--ink);
  }
</style>
</head>
<body>
<main class="stage">
  <section class="card card-front" aria-label="Card front">
    <div class="front-ring"></div>
    <div class="front-brand">GLIMORA</div>
    <div class="front-url">www.glimora-example.com</div>
  </section>

  <section class="card card-back" aria-label="Card back">
    <div class="brand-dot"></div>
    <div class="back-brand">GLIMORA</div>
    <div class="person-name">MARA ELLISON</div>
    <div class="person-role">CEO/FOUNDER</div>
    <div class="address">4120 Willow Crest Road<br>Fairbanks, Alaska 99701</div>
    <svg class="contact-rule" width="250" height="30" viewBox="0 0 250 30" aria-hidden="true">
      <g fill="none" stroke="#b97f98" stroke-width="1.6">
        <line x1="0" y1="15" x2="78" y2="15"/>
        <line x1="172" y1="15" x2="250" y2="15"/>
        <circle cx="92" cy="15" r="11"/>
        <circle cx="125" cy="15" r="11"/>
        <circle cx="158" cy="15" r="11"/>
        <line x1="103" y1="15" x2="114" y2="15"/>
        <line x1="136" y1="15" x2="147" y2="15"/>
      </g>
      <path d="M88 9 q-2 1 -1 4 q2 5 7 7 q3 1 4 -1 l-2 -2 q-1 0 -2 1 q-3 -1 -4 -4 q1 -1 1 -2 z" fill="#b97f98"/>
      <rect x="119" y="11" width="12" height="8" fill="#b97f98"/>
      <path d="M119 11 l6 5 l6 -5" fill="none" stroke="#f7f7f7" stroke-width="1"/>
      <circle cx="158" cy="15" r="5.5" fill="#b97f98"/>
      <ellipse cx="158" cy="15" rx="2.2" ry="5.5" fill="none" stroke="#f7f7f7" stroke-width="0.9"/>
    </svg>
    <div class="contacts">555 218 4406<br>info@glimora-example.com<br>www.glimora-example.com</div>
  </section>
</main>
</body>
</html>
```